Specialised investor in e-mobility and energy wants business card design

We need a business card design that fits our existing corporate design. <The look and feel must be 'sharp'/'clean', dynamic, communicate momentum, professionalism etc (as one would imagine from a firm in the financial sector). We like the idea of a reverse-side of the card that includes the logo, and the name and contact details on the other. We expect the deliverable to be whatever format might be required to be able to get cards printed directly by a service such as kelmo press. Our website is www.zub.capital

```html
<!DOCTYPE html>
<html lang="en">
<head>
<meta charset="utf-8">
<title>ZUB Capital – Business Card</title>
<link href="https://fonts.googleapis.com/css2?family=Lato:wght@400;700;900&display=swap" rel="stylesheet">
<style>
  :root {
    --backdrop: #1c1c1c;
    --card: #ffffff;
    --green-dark: #2e5424;
    --green-light: #7ab648;
    --ink: #3a3a3a;
  }
  * { margin: 0; padding: 0; box-sizing: border-box; }
  html, body {
    width: 1200px;
    height: 1122px;
    overflow: hidden;
    background: var(--backdrop);
    font-family: 'Lato', sans-serif;
  }
  .stage {
    position: relative;
    width: 1200px;
    height: 1122px;
  }
  .card {
    position: absolute;
    left: 250px;
    width: 700px;
    height: 400px;
    background: var(--card);
    border-radius: 26px;
    box-shadow: 0 10px 30px rgba(0,0,0,.5);
  }
  .card--back { top: 111px; }
  .card--front { top: 611px; }

  .wordmark {
    display: flex;
    align-items: center;
    gap: 14px;
    color: var(--green-dark);
    font-weight: 400;
    white-space: nowrap;
  }
  .wordmark__dot {
    border-radius: 50%;
    background: var(--green-light);
  }
  .card--back .wordmark {
    position: absolute;
    left: 50%;
    top: 50%;
    transform: translate(-50%, -50%);
    font-size: 74px;
    letter-spacing: 1px;
  }
  .card--back .wordmark__dot { width: 26px; height: 26px; }

  .card--front .wordmark {
    position: absolute;
    right: 44px;
    top: 40px;
    font-size: 40px;
    gap: 10px;
  }
  .card--front .wordmark__dot { width: 14px; height: 14px; }

  .person {
    position: absolute;
    left: 48px;
    top: 190px;
  }
  .person__name {
    color: var(--green-dark);
    font-weight: 900;
    font-size: 30px;
    letter-spacing: .5px;
    line-height: 1.1;
  }
  .person__role {
    color: var(--green-light);
    font-size: 19px;
    margin-top: 4px;
  }
  .divider {
    position: absolute;
    left: 48px;
    right: 48px;
    top: 268px;
    height: 1.5px;
    background: var(--green-dark);
  }
  .company {
    position: absolute;
    left: 48px;
    top: 290px;
    font-size: 17px;
    color: var(--ink);
    line-height: 1.5;
  }
  .company__name { color: var(--green-dark); font-weight: 700; }

  .contacts {
    position: absolute;
    left: 372px;
    top: 190px;
    list-style: none;
    font-size: 17px;
    color: var(--ink);
  }
  .contacts li {
    display: flex;
    align-items: center;
    gap: 10px;
    line-height: 1.65;
  }
  .contacts svg { width: 15px; height: 15px; fill: none; stroke: var(--green-light); stroke-width: 2; }
  .contacts .icon-mail { fill: var(--green-light); stroke: #fff; stroke-width: 1.2; }

  .website {
    position: absolute;
    right: 48px;
    top: 205px;
    font-size: 15px;
    color: var(--ink);
    letter-spacing: .3px;
  }
</style>
</head>
<body>
<main class="stage">
  <section class="card card--back" aria-label="Card reverse side">
    <div class="wordmark"><span class="wordmark__dot"></span>ZUB Capital</div>
  </section>

  <section class="card card--front" aria-label="Card front side">
    <div class="wordmark"><span class="wordmark__dot"></span>ZUB Capital</div>

    <div class="person">
      <p class="person__name">MARTEN OAKES</p>
      <p class="person__role">Founder &amp; CEO</p>
    </div>

    <ul class="contacts">
      <li>
        <svg viewBox="0 0 16 16" aria-hidden="true"><rect x="4" y="1.5" width="8" height="13" rx="1.5"/><line x1="7" y1="12" x2="9" y2="12"/></svg>
        +41 79410 5827
      </li>
      <li>
        <svg class="icon-mail" viewBox="0 0 16 16" aria-hidden="true"><rect x="1" y="3" width="14" height="10" rx="1"/><polyline points="1,3.5 8,9 15,3.5"/></svg>
        marten@zub.capital
      </li>
    </ul>

    <p class="website">www.zub.capital</p>

    <div class="divider"></div>

    <div class="company">
      <p class="company__name">ZUB Capital S.A.</p>
      <p>Geneva, Switzerland</p>
    </div>
  </section>
</main>
</body>
</html>
```